Social Media Graphics - Oakline Push REVISED

Create 6-7 individual social media graphics (square size) to encourage folks to join our online course called:

The Harvest Ledger Circle
How to Launch a Multi-Million Business From Scratch
Sign Up Today!

IMPORTANT: Make the largest and most prominent text on the graphic be: How to Launch a Multi-Million Business From Scratch

For the color scheme of the graphics, let's try a blue color palette; make sure the graphics appeal to both men and women

Make sure each graphic contains 1 of the 3 pics attached (crop pic as needed); and make sure one of the graphics is all TEXT only.

Target Market(s)

men and women looking to start a business

Industry/Entity Type

Entrepreneurship

Colors
0054AA
0677BA
7BADD7
CADEEF
E8F1F8

Requirements
Must have
• All the text and use the 3 pics provided; one graphic can be all text; Simple, modern design that's easy to read

```html
<!DOCTYPE html>
<html lang="en">
<head>
<meta charset="utf-8">
<title>How to Launch a Multi-Million Business From Scratch</title>
<link href="https://fonts.googleapis.com/css2?family=Bebas+Neue&family=Montserrat:wght@700;800&display=swap" rel="stylesheet">
<style>
  :root {
    --blue-deep: #0054AA;
    --blue-mid: #0677BA;
    --blue-soft: #7BADD7;
    --blue-pale: #CADEEF;
    --blue-mist: #E8F1F8;
  }
  * { margin: 0; padding: 0; box-sizing: border-box; }
  html, body { width: 1200px; height: 1200px; overflow: hidden; background: var(--blue-deep); }
  .post {
    position: relative;
    width: 1200px;
    height: 1200px;
    background: var(--blue-deep);
    overflow: hidden;
    font-family: "Montserrat", Arial, sans-serif;
  }
  .backdrop { position: absolute; inset: 0; }
  .speaker-photo {
    position: absolute;
    left: 0; top: 0;
    width: 306px; height: 1200px;
    background: linear-gradient(180deg, var(--blue-pale) 0%, var(--blue-soft) 45%, #5f97c9 100%);
    opacity: 0.9;
  }
  .hosts-photo {
    position: absolute;
    left: 0; top: 500px;
    width: 690px; height: 700px;
    border-radius: 320px 320px 0 0;
    background: linear-gradient(180deg, #3c86c6 0%, #1f4f86 55%, #14335a 100%);
  }
  .headline {
    position: absolute;
    left: 366px; top: 38px;
    width: 800px;
    font-family: "Bebas Neue", "Oswald", sans-serif;
    font-size: 126px;
    line-height: 105px;
    letter-spacing: 4px;
    color: var(--blue-mist);
    text-transform: uppercase;
  }
  .course-name {
    position: absolute;
    left: 716px; top: 548px;
    width: 460px;
    font-family: "Montserrat", Arial, sans-serif;
    font-weight: 800;
    font-size: 50px;
    line-height: 60px;
    letter-spacing: 1px;
    color: var(--blue-pale);
    text-transform: uppercase;
    text-shadow: 2px 3px 0 rgba(0, 30, 70, 0.45);
  }
  .cta {
    position: absolute;
    left: 716px; top: 790px;
    width: 363px; height: 76px;
    border-radius: 38px;
    background: var(--blue-mist);
    color: var(--blue-deep);
    display: flex; align-items: center; justify-content: center;
    font-weight: 800;
    font-size: 23px;
    letter-spacing: 0.5px;
    text-transform: uppercase;
  }
</style>
</head>
<body>
  <main class="post">
    <svg class="backdrop" width="1200" height="1200" viewBox="0 0 1200 1200" aria-hidden="true">
      <circle cx="300" cy="190" r="265" fill="#0a4f9c" opacity="0.45"/>
      <circle cx="310" cy="710" r="300" fill="var(--blue-mid)"/>
    </svg>
    <div class="speaker-photo" role="img" aria-label="Photo of the male host speaking on stage with a microphone, tinted light blue"></div>
    <div class="hosts-photo" role="img" aria-label="Photo of the two smiling course hosts: a woman in a red dress with arms crossed and a man in a black jacket"></div>

    <h1 class="headline">How to launch a<br>multi-million<br>business from<br>scratch</h1>
    <p class="course-name">The Harvest<br>Ledger<br>Circle</p>
    <div class="cta">Sign up today!</div>
  </main>
</body>
</html>
```